Veltra Metrics New Website for Health Benefits Plan Decisioneering Tool Launch

Veltra Metrics is a SaaS provider of health benefits comparison tools. We need a new simple SaaS focused website to direct customers to our product

Target Market(s)

General Public comparing their health benefits plans from their employer or from the state exchanges in the US

Coding

Coded - Design and coding required

Number of Pages Required

3 page

Requirements
Must have
• Main page - "Know the Best Health Benefits Plan for You!"
Graphic of a person looking over papers on their desk
Compare Now button to link to SaaS product
About Us
Product Page

https://plimbo.example/top-app-pages/

```html
<!DOCTYPE html>
<html lang="en">
<head>
<meta charset="utf-8">
<title>Veltra Metrics — Know the Best Health Benefits Plan for You</title>
<link rel="stylesheet" href="https://fonts.googleapis.com/css2?family=Cinzel:wght@600;700&family=Roboto:wght@400;500;700&display=swap">
<style>
:root{
  --blue:#2a9ad8;
  --blue-dark:#1f7fb8;
  --ink:#1b1b1b;
  --text:#555;
  --muted:#777;
  --pale:#eef1f6;
  --card:#ffffff;
  --dark:#2b2b2b;
  --star:#f5b800;
}
*{box-sizing:border-box;margin:0;padding:0}
html,body{width:1200px;height:4076px;overflow:hidden}
body{font-family:"Roboto",Arial,sans-serif;color:var(--text);background:#fff;position:relative}
.wrap{width:978px;margin:0 auto;position:relative}
.display{font-family:"Cinzel",Georgia,serif;font-weight:700;color:var(--ink);letter-spacing:.5px}
.display .accent{color:var(--blue)}
.btn{display:inline-flex;align-items:center;gap:8px;background:var(--blue);color:#fff;font-weight:700;font-size:14px;text-transform:uppercase;padding:0 20px;height:44px;border-radius:2px}
.btn .dot{width:13px;height:13px;border-radius:50%;background:#fff;display:inline-block;position:relative}
.btn .dot:after{content:"";position:absolute;left:3px;top:4px;border-left:5px solid var(--blue);border-top:2.5px solid transparent;border-bottom:2.5px solid transparent}

/* header */
.site-header{height:93px;display:flex;align-items:center}
.site-header .wrap{display:flex;align-items:center}
.brand{font-size:22px;font-weight:500;color:var(--blue);letter-spacing:.5px;display:flex;align-items:center;gap:8px}
.brand .mark{width:10px;height:10px;border-radius:50%;background:var(--blue)}
.main-nav{display:flex;gap:28px;margin-left:auto;font-size:15px;color:var(--ink);align-items:center}
.main-nav .active{color:var(--blue);position:relative}
.main-nav .active:before{content:"";position:absolute;top:-11px;left:50%;width:7px;height:7px;border-radius:50%;background:var(--blue);transform:translateX(-50%)}
.nav-phone{display:flex;gap:6px;align-items:center;margin-left:14px}
.sign-in{margin-left:36px;height:40px;width:116px;justify-content:center;font-size:14px;padding:0}

/* hero */
.hero{position:relative;height:652px;background:linear-gradient(180deg,#eceef2,#dfe4ea)}
.hero-photo{position:absolute;inset:0;background:linear-gradient(100deg,#f2f1ee 0%,#e6dfd6 45%,#cdbda9 70%,#dcd6cc 100%)}
.hero-base{position:absolute;left:0;bottom:0;width:1200px;height:150px}
.hero-copy{position:absolute;left:111px;top:178px}
.hero-copy h1{font-size:41px;line-height:44px;font-variant:small-caps}
.hero-copy .btn{margin-top:43px;height:48px;width:193px;justify-content:center;padding:0}

/* about */
.about{height:590px;background:var(--pale);text-align:center;padding-top:68px}
.section-title{font-size:36px;font-variant:small-caps}
.lead{font-size:14px;line-height:25px;color:var(--text);margin:16px auto 0;width:850px}
.features{display:flex;gap:21px;margin-top:50px}
.feature{flex:1;background:var(--card);height:277px;padding-top:30px;box-shadow:0 2px 10px rgba(0,0,0,.05)}
.feature .icon{width:94px;height:94px;border-radius:50%;background:linear-gradient(160deg,#3cb2ec,#1a78c0);margin:0 auto;display:flex;align-items:center;justify-content:center}
.feature h3{font-size:17px;color:var(--ink);margin-top:28px;font-weight:700}
.feature p{font-size:14px;line-height:22px;margin:16px 40px 0}

/* saas */
.saas{height:1567px;padding-top:82px;text-align:center;background:#fff;position:relative;overflow:hidden}
.saas .section-title{font-size:34px;line-height:42px}
.saas .lead{width:910px}
.row{display:flex;align-items:center;justify-content:space-between;text-align:left;position:relative}
.row-copy{width:456px}
.row-copy h2{font-size:28px;line-height:37px;color:var(--ink);font-weight:500}
.row-copy p{font-size:14px;line-height:26px;text-align:justify;margin-top:30px}
.row-copy .btn{margin-top:32px;height:44px}
.shot-wrap{width:453px;height:330px;position:relative}
.shot-back{position:absolute;left:-60px;right:-60px;top:-20px;bottom:-20px;background:linear-gradient(135deg,rgba(215,228,240,.0),rgba(215,228,240,.7));clip-path:polygon(50% 0,100% 50%,50% 100%,0 50%)}
.shot{position:absolute;inset:0;background:#f6f8fb;border:1px solid #dfe6ee;box-shadow:0 6px 24px rgba(80,120,160,.25);display:flex}
.shot .side{width:70px;background:#eef2f6;padding:30px 8px}
.shot .side i{display:block;height:5px;background:#cfd7e0;margin-bottom:11px;border-radius:2px}
.shot .side i.on{background:var(--star);height:8px}
.shot .main{flex:1;padding:22px 14px}
.shot .bar-top{height:8px;background:#e3e8ee;margin-bottom:18px;border-radius:2px}
.trow{display:flex;gap:10px;align-items:center;height:21px;border-bottom:1px solid #e7ecf1}
.trow span{height:4px;background:#c9d2dc;border-radius:2px}
.trow b{height:4px;width:50px;background:var(--star);border-radius:2px}

/* testimonials */
.clients{height:518px;background:var(--pale);text-align:center;padding-top:58px}
.quotes{display:flex;gap:21px;margin-top:90px}
.quote{flex:1;position:relative}
.quote .box{background:#fff;height:188px;border-top:3px solid var(--blue);border-radius:8px 8px 4px 4px;padding:70px 26px 0;font-size:14px;line-height:26px;color:#444}
.quote .avatar{position:absolute;left:50%;top:-46px;transform:translateX(-50%);width:92px;height:92px;border-radius:50%;border:3px solid #fff;background:linear-gradient(160deg,#cfd6de,#8a97a6);box-shadow:0 0 0 1px #d8e2ea}
.quote .who{margin-top:22px;font-size:14px;color:var(--ink);font-weight:500}
.quote .who small{font-size:10px;font-weight:400;color:#444}
.stars{color:var(--star);font-size:13px;letter-spacing:1px;margin-top:4px}

/* cta */
.cta{height:283px;background:linear-gradient(90deg,#2d9ad6,#2690cf 60%,#3aa3db);text-align:center;color:#fff;padding-top:57px}
.cta h2{font-family:"Cinzel",Georgia,serif;font-weight:700;font-size:38px;letter-spacing:1px;color:#fff}
.cta p{font-size:14px;line-height:24px;margin-top:14px}
.cta .btn{background:var(--dark);margin-top:26px;height:46px}

/* footer */
.site-footer{height:373px;position:relative}
.footer-grid{display:flex;padding-top:65px}
.footer-brand{width:285px;padding-top:60px}
.socials{display:flex;gap:7px;margin:22px 0 0 22px}
.socials span{width:32px;height:32px;border:1.5px solid var(--ink);border-radius:50%}
.footer-col h4{font-size:15px;color:var(--ink);font-weight:500;margin-bottom:28px}
.footer-col ul{list-style:none;font-size:13px;line-height:26px;color:var(--muted)}
.col-links{width:165px}
.col-prod{width:309px}
.col-prod .lists{display:flex;gap:40px}
.contact-item{display:flex;gap:10px;margin-bottom:18px;font-size:13px;color:var(--muted);line-height:17px}
.contact-item strong{color:var(--ink);font-weight:500;display:block}
.footer-bottom{position:absolute;left:111px;right:111px;top:317px;border-top:1px solid #e2e2e2;text-align:center;font-size:14px;color:#555;padding-top:18px}
.to-top{position:absolute;right:58px;top:295px;width:34px;height:34px;border-radius:50%;background:var(--blue);display:flex;align-items:center;justify-content:center}
</style>
</head>
<body>

<header class="site-header">
  <div class="wrap">
    <div class="brand"><span class="mark"></span>VELTRA METRICS</div>
    <nav class="main-nav">
      <span class="active">Home</span><span>About Us</span><span>Products</span><span>Contact Us</span>
      <span class="nav-phone"><svg width="13" height="13" viewBox="0 0 24 24"><path fill="#2a9ad8" d="M6.6 10.8a15 15 0 006.6 6.6l2.2-2.2c.3-.3.7-.4 1-.2 1.1.4 2.3.6 3.6.6.6 0 1 .4 1 1V20c0 .6-.4 1-1 1A17 17 0 013 4c0-.6.4-1 1-1h3.5c.6 0 1 .4 1 1 0 1.3.2 2.5.6 3.6.1.3 0 .7-.2 1z"/></svg>(555)-218-0937</span>
    </nav>
    <span class="btn sign-in"><svg width="11" height="12" viewBox="0 0 11 12"><rect x="1" y="5" width="9" height="7" fill="#fff"/><path d="M3 5V3.5a2.5 2.5 0 015 0V5" stroke="#fff" stroke-width="1.5" fill="none"/></svg>Sign In</span>
  </div>
</header>

<section class="hero">
  <div class="hero-photo" role="img" aria-label="Photo of a woman at her desk reviewing papers beside a laptop in a bright office"></div>
  <svg class="hero-base" viewBox="0 0 1200 150" preserveAspectRatio="none">
    <polygon points="0,150 0,60 598,128 1200,30 1200,150" fill="#e9edf2"/>
    <polyline points="0,58 598,128 1200,28" fill="none" stroke="#2a8fd0" stroke-width="6"/>
    <polygon points="0,150 0,60 598,128 1200,30 1200,150" fill="#e9edf2"/>
  </svg>
  <div class="hero-copy">
    <h1 class="display">Know the <span class="accent">Best<br>Health Benefits</span><br>Plan for You!</h1>
    <span class="btn">Compare Now <i class="dot"></i></span>
  </div>
</section>

<section class="about">
  <div class="wrap">
    <h2 class="display section-title">About Veltra <span class="accent">Metrics</span></h2>
    <p class="lead">Lorem ipsum dolor sit amet, consectetur adipiscing elit, sed do eiusmod tempor incididunt ut labore et dolore magna aliqua. Ut enim ad minim veniam, quis</p>
    <div class="features">
      <div class="feature"><div class="icon"><svg width="50" height="44" viewBox="0 0 50 44" fill="none" stroke="#fff" stroke-width="2"><path d="M12 24a9 9 0 010-18 12 12 0 0123 2 8 8 0 012 16"/><rect x="14" y="20" width="22" height="22" rx="2"/><circle cx="25" cy="31" r="6"/></svg></div><h3>WORK ANYWHERE</h3><p>Sed ut perspiciatis unde omnis iste natus error sit voluptatem accusantium doloremque laudantium,</p></div>
      <div class="feature"><div class="icon"><svg width="52" height="44" viewBox="0 0 52 44" fill="none" stroke="#fff" stroke-width="2"><path d="M14 20a9 9 0 010-18 12 12 0 0123 2 8 8 0 012 16"/><rect x="10" y="22" width="32" height="16" rx="1"/><path d="M4 42h44"/></svg></div><h3>CAPTURE WHAT MATTERS</h3><p>Sed ut perspiciatis unde omnis iste natus error sit voluptatem accusantium doloremque laudantium,</p></div>
      <div class="feature"><div class="icon"><svg width="52" height="46" viewBox="0 0 52 46" fill="none" stroke="#fff" stroke-width="2"><path d="M12 24a9 9 0 010-18 12 12 0 0123 2 8 8 0 012 16"/><circle cx="26" cy="20" r="6"/><path d="M14 30v12M22 30v12M30 30v12M38 30v12"/></svg></div><h3>YOUR NOTES, YOUR WAY</h3><p>Sed ut perspiciatis unde omnis iste natus error sit voluptatem accusantium doloremque laudantium,</p></div>
    </div>
  </div>
</section>

<section class="saas">
  <div class="wrap">
    <h2 class="display section-title">SaaS Dedicated of<br><span class="accent" style="font-variant:normal">HEALTH BENEFITS COMPARISON</span></h2>
    <p class="lead">Sed ut perspiciatis unde omnis iste natus error sit voluptatem accusantium doloremque laudantium, totam rem aperiam, eaque ipsa quae ab illo inventore veritatis et &nbsp;quasi architecto beatae vitae</p>

    <div class="row" style="margin-top:68px">
      <div class="row-copy">
        <h2>Lorem ipsum dolor sit amet, consectetur elit</h2>
        <p>Sed ut perspiciatis unde omnis iste natus error sit voluptatem accusantium doloremque laudantium, totam rem aperiam, eaque ipsa quae ab illo inventore veritatis et quasi architecto beatae vitae dicta sunt explicabo. Nemo enim ipsam voluptatem quia voluptas sit aspernatur aut odit aut fugit, sed quia consequuntur magni dolores eos qui ratione voluptatem sequi nesciunt.</p>
        <span class="btn">Learn More <i class="dot"></i></span>
      </div>
      <div class="shot-wrap" role="img" aria-label="Product dashboard showing a table of plans"><div class="shot-back"></div>
        <div class="shot"><div class="side"><i class="on"></i><i></i><i></i><i></i><i></i><i></i><i></i></div>
          <div class="main"><div class="bar-top"></div>
            <div class="trow"><span style="width:30px"></span><span style="width:60px"></span><span style="width:50px"></span><span style="width:70px"></span><b></b></div>
            <div class="trow"><span style="width:30px"></span><span style="width:55px"></span><span style="width:50px"></span><span style="width:80px"></span><b></b></div>
            <div class="trow"><span style="width:30px"></span><span style="width:62px"></span><span style="width:45px"></span><span style="width:66px"></span><b></b></div>
            <div class="trow"><span style="width:30px"></span><span style="width:50px"></span><span style="width:50px"></span><span style="width:74px"></span><b></b></div>
            <div class="trow"><span style="width:30px"></span><span style="width:58px"></span><span style="width:48px"></span><span style="width:70px"></span><b></b></div>
            <div class="trow"><span style="width:30px"></span><span style="width:60px"></span><span style="width:50px"></span><span style="width:62px"></span><b></b></div>
            <div class="trow"><span style="width:30px"></span><span style="width:54px"></span><span style="width:52px"></span><span style="width:78px"></span><b></b></div>
            <div class="trow"><span style="width:30px"></span><span style="width:60px"></span><span style="width:46px"></span><span style="width:70px"></span><b></b></div>
            <div class="trow"><span style="width:30px"></span><span style="width:52px"></span><span style="width:50px"></span><span style="width:72px"></span><b></b></div>
            <div class="trow"><span style="width:30px"></span><span style="width:58px"></span><span style="width:50px"></span><span style="width:68px"></span><b></b></div>
          </div></div>
      </div>
    </div>

    <div class="row" style="margin-top:85px">
      <div class="shot-wrap" role="img" aria-label="Product dashboard with bar chart and calendar"><div class="shot-back"></div>
        <div class="shot"><div class="side"><i class="on"></i><i></i><i></i><i></i><i></i><i></i><i></i></div>
          <div class="main"><div class="bar-top"></div>
            <svg width="350" height="260" viewBox="0 0 350 260">
              <g fill="#2b3a4e"><rect x="10" y="60" width="4" height="50"/><rect x="32" y="40" width="4" height="70"/><rect x="54" y="70" width="4" height="40"/><rect x="76" y="30" width="4" height="80"/><rect x="98" y="55" width="4" height="55"/><rect x="120" y="45" width="4" height="65"/><rect x="142" y="65" width="4" height="45"/><rect x="164" y="35" width="4" height="75"/><rect x="186" y="50" width="4" height="60"/></g>
              <g fill="#f5b800"><rect x="16" y="40" width="4" height="70"/><rect x="38" y="60" width="4" height="50"/><rect x="60" y="35" width="4" height="75"/><rect x="82" y="55" width="4" height="55"/><rect x="104" y="30" width="4" height="80"/><rect x="126" y="60" width="4" height="50"/><rect x="148" y="40" width="4" height="70"/><rect x="170" y="55" width="4" height="55"/><rect x="192" y="35" width="4" height="75"/></g>
              <rect x="220" y="10" width="120" height="110" fill="#fff" stroke="#e3e8ee"/>
              <circle cx="280" cy="50" r="16" fill="#e3e8ee"/>
              <path d="M10 160l15-12 12 10 14-16 12 14" fill="none" stroke="#e2456b" stroke-width="2"/>
              <path d="M120 160l15-12 12 10 14-16 12 14" fill="none" stroke="#2fb37a" stroke-width="2"/>
              <path d="M230 160l15-12 12 10 14-16 12 14" fill="none" stroke="#2a9ad8" stroke-width="2"/>
              <rect x="10" y="190" width="100" height="60" fill="#fff" stroke="#e3e8ee"/><rect x="120" y="190" width="100" height="60" fill="#fff" stroke="#e3e8ee"/><rect x="230" y="190" width="110" height="60" fill="#fff" stroke="#e3e8ee"/>
            </svg>
          </div></div>
      </div>
      <div class="row-copy">
        <h2>Lorem ipsum dolor sit amet, consectetur elit</h2>
        <p>Sed ut perspiciatis unde omnis iste natus error sit voluptatem accusantium doloremque laudantium, totam rem aperiam, eaque ipsa quae ab illo inventore veritatis et quasi architecto beatae vitae dicta sunt explicabo. Nemo enim ipsam voluptatem quia voluptas sit aspernatur aut odit aut fugit, sed quia consequuntur magni dolores eos qui ratione voluptatem sequi nesciunt.</p>
        <span class="btn">Learn More <i class="dot"></i></span>
      </div>
    </div>

    <div class="row" style="margin-top:85px">
      <div class="row-copy">
        <h2>Lorem ipsum dolor sit amet, consectetur elit</h2>
        <p>Sed ut perspiciatis unde omnis iste natus error sit voluptatem accusantium doloremque laudantium, totam rem aperiam, eaque ipsa quae ab illo inventore veritatis et quasi architecto beatae vitae dicta sunt explicabo. Nemo enim ipsam voluptatem quia voluptas sit aspernatur aut odit aut fugit, sed quia consequuntur magni dolores eos qui ratione voluptatem sequi nesciunt.</p>
        <span class="btn">Learn More <i class="dot"></i></span>
      </div>
      <div class="shot-wrap" role="img" aria-label="Product chat screen with message list"><div class="shot-back"></div>
        <div class="shot"><div class="side"><i></i><i></i><i class="on"></i><i></i><i></i><i></i><i></i></div>
          <div class="main"><div class="bar-top"></div>
            <svg width="350" height="260" viewBox="0 0 350 260">
              <g fill="#fff" stroke="#e3e8ee"><rect x="0" y="0" width="110" height="255"/><rect x="120" y="0" width="230" height="255"/></g>
              <g fill="#d3dae2"><circle cx="14" cy="20" r="6"/><circle cx="14" cy="50" r="6"/><circle cx="14" cy="80" r="6"/><circle cx="14" cy="110" r="6"/><circle cx="14" cy="140" r="6"/><circle cx="14" cy="170" r="6"/><circle cx="14" cy="200" r="6"/><circle cx="14" cy="230" r="6"/></g>
              <g fill="#c9d2dc"><rect x="26" y="18" width="60" height="4"/><rect x="26" y="48" width="55" height="4"/><rect x="26" y="78" width="62" height="4"/><rect x="26" y="108" width="50" height="4"/><rect x="26" y="138" width="58" height="4"/><rect x="26" y="168" width="52" height="4"/><rect x="26" y="198" width="60" height="4"/><rect x="26" y="228" width="54" height="4"/></g>
              <rect x="140" y="20" width="150" height="30" fill="#f0f3f6"/><rect x="210" y="70" width="120" height="14" fill="#f5b800"/><rect x="140" y="110" width="150" height="30" fill="#f0f3f6"/><rect x="140" y="170" width="150" height="30" fill="#f0f3f6"/><rect x="140" y="230" width="190" height="14" fill="#f0f3f6"/>
            </svg>
          </div></div>
      </div>
    </div>
  </div>
</section>

<section class="clients">
  <div class="wrap">
    <h2 class="display section-title" style="font-size:40px;font-variant:normal">WHAT OUR <span class="accent">CLIENTS SAY?</span></h2>
    <div class="quotes">
      <div class="quote"><div class="box">Sed ut perspiciatis unde omnis iste natus error sit voluptatem accusantium doloremque laudantium, totam rem aperiam, eaque ipsa quae ab illo</div><div class="avatar" role="img" aria-label="Client portrait"></div><div class="who">Nora Ellery, <small>Chairman KLT</small></div><div class="stars">★★★★★</div></div>
      <div class="quote"><div class="box">Sed ut perspiciatis unde omnis iste natus error sit voluptatem accusantium doloremque laudantium, totam rem aperiam, eaque ipsa quae ab illo</div><div class="avatar" role="img" aria-label="Client portrait"></div><div class="who">Ivy Tanaka, <small>Project Manager</small></div><div class="stars">★★★★★</div></div>
      <div class="quote"><div class="box">Lorem ipsum dolor sit consectetur adipiscing elit, sed do eiusmod tempor incididunt ut labore et dolore magna aliqua. Ut enim ad minim veniam,</div><div class="avatar" role="img" aria-label="Client portrait"></div><div class="who">Owen Hale, <small>Chairman KLT</small></div><div class="stars">★★★★★</div></div>
    </div>
  </div>
</section>

<section class="cta">
  <h2>CHOOSE A BETTER WAY TO WORK</h2>
  <p>Lorem ipsum dolor sit amet, consectetur adipiscing elit, sed do eiusmod tempor incididunt ut labore et dolore magna aliqua.<br>Ut enim ad minim veniam,quis nostrud exercitation ullamco laboris</p>
  <span class="btn">Compare Now <i class="dot" style="--x:0"></i></span>
</section>

<footer class="site-footer">
  <div class="wrap footer-grid">
    <div class="footer-brand">
      <div class="brand"><span class="mark"></span>VELTRA METRICS</div>
      <div class="socials" aria-label="Social media links"><span></span><span></span><span></span><span></span></div>
    </div>
    <div class="footer-col col-links"><h4>Quick Links</h4><ul><li>Home</li><li>Products</li><li>About Us</li><li>Careers</li><li>Press</li></ul></div>
    <div class="footer-col col-prod"><h4>Products</h4><div class="lists"><ul><li>How It Works</li><li>Pricing</li><li>Security</li><li>Features</li></ul><ul><li>Education</li><li>Tools &amp; Guides</li><li>FAQ</li><li>Customer Reviews</li><li>Privacy Policy</li><li>Terms of Use</li></ul></div></div>
    <div class="footer-col"><h4>Contact Us</h4>
      <div class="contact-item"><svg width="13" height="13" viewBox="0 0 24 24"><path fill="#2a9ad8" d="M6.6 10.8a15 15 0 006.6 6.6l2.2-2.2c.3-.3.7-.4 1-.2 1.1.4 2.3.6 3.6.6.6 0 1 .4 1 1V20c0 .6-.4 1-1 1A17 17 0 013 4c0-.6.4-1 1-1h3.5c.6 0 1 .4 1 1 0 1.3.2 2.5.6 3.6.1.3 0 .7-.2 1z"/></svg><div><strong>Phone</strong>(555)-218-0937</div></div>
      <div class="contact-item"><svg width="13" height="13" viewBox="0 0 24 24"><rect x="2" y="5" width="20" height="14" fill="#2a9ad8"/><path d="M2 5l10 8 10-8" stroke="#fff" stroke-width="1.5" fill="none"/></svg><div><strong>Email</strong>hello@veltrametrics.example</div></div>
      <div class="contact-item"><svg width="13" height="14" viewBox="0 0 24 26"><path fill="#2a9ad8" d="M12 0a9 9 0 00-9 9c0 7 9 17 9 17s9-10 9-17a9 9 0 00-9-9zm0 12a3 3 0 110-6 3 3 0 010 6z"/></svg><div><strong>Location</strong>420 Larkspur Avenue, 3rd<br>Floor, Maple Grove, CO 80000</div></div>
    </div>
  </div>
  <div class="to-top"><svg width="14" height="9" viewBox="0 0 14 9"><path d="M1 8l6-6 6 6" stroke="#fff" stroke-width="2" fill="none"/></svg></div>
  <div class="footer-bottom">2020 Copyright - Veltra Metrics &nbsp;|&nbsp; All Rights Reserved</div>
</footer>

</body>
</html>
```